New business card, letter head, email signature and Portfolio for our Security company.

We are an Crest security company that provides a top quality manpower services to protect high rise buildings, retail and all type of properties and would like a new business card/logo look.

- We would like the spot UV design.
- Matt black (double sided).
- We would like to incorporate a royal blue colour (feel free to experiment with it).
- Feel free to try different lengths with the card to make it stand out more than a normal business card.
- We would like the logo to be an eagle eye in the background (shines when card is tilted slightly in the background, either on the front, back or both sides of the card). Image attached as an example of eye shape (colour to be either black or royal blue).
- HARBOUR CREST SECURITY SERVICES PTY. LTD. and HCSS to be placed on one side of the card and on the other side of the card to have;

- Name in slightly bigger font than the position (directly on the bottom on the name).
- Mobile number
- Email address
- Website email address
- PO BOX address

Can we please have the files in a format that we can edit.

Reason: I need to consult my business partner with the designs so far and will make a decision from there.

Target Market(s)

Security Industry

Industry/Entity Type

Business

Contact Information for Business Card

- Mobile number
- Email address
- Website email address
- PO BOX address

Logo Text

HCSS and underneath the HCSS please add HARBOUR CREST SECURITY SERVICES PTY. LTD.

Font styles to use
Other font styles liked:
• bold type font

Colors
0255a3
000000

Requirements
Must have
• We are an Crest security company that provides a top quality manpower services to protect high rise buildings, retail and all type of properties and would like a new business card/logo look.
• - We would like the spot UV design.
• - Matt black (double sided).
• - We would like to incorporate a royal blue colour (feel free to experiment with it).
• - Feel free to try different lengths with the card to make it stand out more than a normal business card.
• - We would like the logo to be an eagle eye in the background (shines when card is tilted slightly in the background, either on the front, back or both sides of the card). Image attached as an example of eye shape (colour to be either black or royal blue).
• - HARBOUR CREST SECURITY SERVICES PTY. LTD. and HCSS to be placed on one side of the card and on the other side of the card to have;
• - Name in slightly bigger font than the position (directly on the bottom on the name).
• - Mobile number
• - Email address
• - Website email address
• - PO BOX address
• Can we please have the files in a format that we can edit.
Nice to have
• Feel free to try different lengths with the card to make it stand out more than a normal business card.
• Please find "URBAN JUNGLE" font attached and incorporate HCSS into the same style with building's inside the HCSS bold front also add HARBOUR into the bottom part of the S and follow on E - Crest on the bottom S - SECURITY on the bottom S - SERVICES on the bottom of each letter.
• other than that, I'll be happy with a bold modern font for the HCSS and HARBOUR CREST SECURITY SERVICES in a bold and thinner font underneath.

```html
<!DOCTYPE html>
<html lang="en">
<head>
<meta charset="utf-8">
<title>Harbour Crest Security – Business Card</title>
<link rel="stylesheet" href="https://fonts.googleapis.com/css2?family=Saira:wght@600;700&family=Exo+2:wght@400;500&display=swap">
<style>
  :root {
    --backdrop: #2b2b2d;
    --royal: #2c3a9c;
    --royal-deep: #222f88;
    --navy-text: #1f2a7a;
    --ink: #1c1c22;
    --grey-text: #4a4a52;
    --paper: #ffffff;
  }
  * { box-sizing: border-box; margin: 0; padding: 0; }
  html, body {
    width: 1200px; height: 1000px; overflow: hidden;
    background: var(--backdrop);
  }
  .stage { position: relative; width: 1200px; height: 1000px; }

  .card {
    position: absolute;
    border-radius: 24px;
    overflow: hidden;
  }

  /* Front side */
  .card-front {
    left: 240px; top: 50px; width: 820px; height: 420px;
    background: linear-gradient(135deg, var(--royal) 0%, var(--royal-deep) 100%);
  }
  .front-brand {
    position: absolute; left: 0; right: 0; top: 160px;
    text-align: center;
    color: var(--paper);
    font-family: "Saira", sans-serif; font-weight: 700;
  }
  .front-brand .brand-name { font-size: 40px; letter-spacing: 1px; line-height: 1.1; }
  .front-brand .brand-sub { font-size: 15px; letter-spacing: 2px; margin-top: 6px; }

  /* Back side */
  .card-back {
    left: 150px; top: 510px; width: 860px; height: 450px;
    background: var(--paper);
  }
  .back-art { position: absolute; inset: 0; }

  .back-brand {
    position: absolute; right: 60px; top: 60px;
    text-align: right;
    color: var(--ink);
    font-family: "Saira", sans-serif; font-weight: 700;
  }
  .back-brand .brand-name { font-size: 30px; letter-spacing: 0.5px; line-height: 1.1; }
  .back-brand .brand-sub { font-size: 12px; letter-spacing: 1.5px; margin-top: 4px; }

  .person { position: absolute; left: 60px; top: 175px; }
  .person-name {
    font-family: "Saira", sans-serif; font-weight: 700;
    font-size: 44px; letter-spacing: 1.5px; line-height: 1;
    color: var(--navy-text);
  }
  .person-role {
    font-family: "Exo 2", sans-serif; font-weight: 400;
    font-size: 25px; line-height: 32px; color: var(--grey-text); margin-top: 6px;
  }

  .contacts {
    position: absolute; left: 60px; top: 285px;
    list-style: none;
    font-family: "Exo 2", sans-serif; font-size: 21px; color: var(--ink);
  }
  .contacts li { display: flex; align-items: center; gap: 18px; height: 34px; }
  .contacts svg { width: 16px; height: 16px; fill: var(--navy-text); flex: none; }
  .contacts .accent { color: var(--navy-text); }

  .address {
    position: absolute; right: 60px; top: 322px;
    font-family: "Exo 2", sans-serif; font-size: 21px; line-height: 30px;
    color: var(--grey-text);
    display: flex; gap: 14px; align-items: flex-start;
  }
  .address svg { width: 18px; height: 24px; fill: var(--navy-text); margin-top: -2px; order: 2; }
</style>
</head>
<body>
<main class="stage">

  <section class="card card-front" aria-label="Business card front">
    <div class="front-brand">
      <div class="brand-name">HARBOUR CREST SECURITY</div>
      <div class="brand-sub">SERVICES PTY. LTD. and HCSS</div>
    </div>
  </section>

  <section class="card card-back" aria-label="Business card back">
    <svg class="back-art" viewBox="0 0 860 450" aria-hidden="true">
      <line x1="228" y1="250" x2="860" y2="298" stroke="var(--navy-text)" stroke-width="2.5"/>
      <polygon points="0,428 560,428 585,402 860,402 860,450 0,450" fill="var(--royal)"/>
    </svg>

    <div class="back-brand">
      <div class="brand-name">HARBOUR CREST SECURITY</div>
      <div class="brand-sub">SERVICES PTY. LTD. and HCSS</div>
    </div>

    <div class="person">
      <div class="person-name">DANIEL HARTLEY</div>
      <div class="person-role">Ceo &amp; Founder</div>
    </div>

    <ul class="contacts">
      <li>
        <svg viewBox="0 0 16 16"><path d="M3.5 1.5l2.5 0 1 3.5-1.8 1.2a8 8 0 0 0 4.6 4.6L11 9l3.5 1v2.5c0 1-1 2-2 2C6.5 14.5 1.5 9.5 1.5 3.5c0-1 1-2 2-2z"/></svg>
        +000 123 456 789
      </li>
      <li>
        <svg viewBox="0 0 16 16"><path d="M1 3h14v10H1z M1.5 3.5L8 8.5l6.5-5" stroke="#fff" stroke-width="1.2"/></svg>
        yourname@email.com
      </li>
      <li>
        <svg viewBox="0 0 16 16"><circle cx="8" cy="8" r="7"/><path d="M1 8h14M8 1c-3 3-3 11 0 14M8 1c3 3 3 11 0 14" stroke="#fff" stroke-width="1" fill="none"/></svg>
        <span>www.<span class="accent">websitename</span>.com</span>
      </li>
    </ul>

    <div class="address">
      <svg viewBox="0 0 18 24"><path d="M9 0a8 8 0 0 0-8 8c0 6 8 16 8 16s8-10 8-16a8 8 0 0 0-8-8zm0 11a3 3 0 1 1 0-6 3 3 0 0 1 0 6z"/></svg>
      <div>Your Street Address<br>NewYork City, 1234</div>
    </div>
  </section>

</main>
</body>
</html>
```